Lanternfield Drinks business cards

We need a business card design for our new logo. The company is modern, progressive, professional, yet approachable. The key products are ready to drink bottles and cans of coffee based beverages.
These cards will be a critical part of the first impression made by our sales organization, business development team, and all external facing personnel.
Card can be a vertical or horizontal orientation.

Target Market(s)

Customers, suppliers, business partners

Industry/Entity Type

Business

Contact Information for Business Card

Business cards should feature Company Name and Logo.

Font styles to use
Serif

Colors

Designer to choose colors to be used in the design.

Requirements
Must have
• Strong readability of Name, phone #, mobile number and email address.
• Job title, website url, Street Address, and other details can be secondary level readability.
Nice to have
• High impact, simplistic quality design.
• Ok to utilize the 'H in the box' separate from the company name

```html
<!DOCTYPE html>
<html lang="en">
<head>
<meta charset="utf-8">
<title>Lanternfield Drinks business cards</title>
<link rel="stylesheet" href="https://fonts.googleapis.com/css2?family=Crimson+Text:ital,wght@0,400;0,600;0,700;1,400&display=swap">
<style>
  :root {
    --backdrop: #3b3b3d;
    --card: #1e1e20;
    --orange: #e35a2e;
    --amber: #f0962c;
    --ink: #f2f2f2;
  }
  * { box-sizing: border-box; margin: 0; padding: 0; }
  html, body { width: 799px; height: 1200px; overflow: hidden; }
  body {
    background: var(--backdrop);
    font-family: "Crimson Text", Georgia, serif;
    position: relative;
  }
  .card {
    position: absolute;
    left: 60px;
    width: 680px;
    height: 390px;
    background: var(--card);
    border-radius: 4px;
    box-shadow: 0 14px 30px rgba(0,0,0,.45);
    overflow: hidden;
  }
  .card--front { top: 90px; }
  .card--back { top: 710px; }

  .brand { display: flex; align-items: center; gap: 14px; color: var(--orange); font-weight: 700; letter-spacing: 1px; text-transform: uppercase; }
  .brand__square { border: 4px solid var(--orange); flex: none; }

  .card--front .brand { position: absolute; top: 130px; left: 0; right: 0; justify-content: center; font-size: 38px; }
  .card--front .brand__square { width: 46px; height: 46px; }
  .front__url {
    position: absolute; top: 262px; left: 0; right: 0;
    display: flex; justify-content: center; align-items: center; gap: 22px;
    color: var(--ink); font-size: 22px;
  }
  .front__url .accent { color: var(--orange); }
  .front__dash { width: 58px; height: 5px; background: var(--orange); border-radius: 3px; }

  .card--back .brand { position: absolute; top: 118px; left: 36px; font-size: 24px; gap: 10px; }
  .card--back .brand__square { width: 34px; height: 34px; border-width: 3px; }

  .contact { position: absolute; top: 100px; left: 380px; color: var(--ink); }
  .contact__name { color: var(--orange); font-size: 28px; font-weight: 700; line-height: 1; }
  .contact__title { font-style: italic; font-size: 16px; margin-top: 4px; margin-bottom: 16px; }
  .contact__row { display: flex; align-items: center; gap: 10px; font-size: 18px; line-height: 1.45; }
  .contact__row svg { width: 16px; height: 16px; fill: var(--orange); flex: none; }
  .contact__address { font-size: 18px; line-height: 1.3; margin-top: 6px; }

  .back__strip { position: absolute; left: 0; bottom: 0; width: 320px; height: 12px; background: var(--amber); }
  .back__tab {
    position: absolute; right: 0; bottom: 0; width: 380px; height: 62px;
    background: var(--orange); border-top-left-radius: 20px;
    color: var(--ink); font-size: 21px; display: flex; align-items: center; padding-left: 48px;
  }
</style>
</head>
<body>
  <section class="card card--front">
    <div class="brand"><span class="brand__square"></span>Lanternfield Drinks</div>
    <div class="front__url">
      <span class="front__dash"></span>
      <span>www.<span class="accent">lanternfielddrinks</span>.com</span>
      <span class="front__dash"></span>
    </div>
  </section>

  <section class="card card--back">
    <div class="brand"><span class="brand__square"></span>Lanternfield Drinks</div>
    <div class="contact">
      <p class="contact__name">Maren Ellis Cole</p>
      <p class="contact__title">Managing Director</p>
      <p class="contact__row">
        <svg viewBox="0 0 16 16" aria-hidden="true"><path d="M2 5c0-2 2-3 6-3s6 1 6 3v1h-3V5H5v1H2zM4 7h8l2 7H2z"/></svg>
        414.208.3391
      </p>
      <p class="contact__row">
        <svg viewBox="0 0 16 16" aria-hidden="true"><path d="M4 0h8a1 1 0 0 1 1 1v14a1 1 0 0 1-1 1H4a1 1 0 0 1-1-1V1a1 1 0 0 1 1-1zm1 2v10h6V2z"/></svg>
        414.762.1058
      </p>
      <p class="contact__row">
        <svg viewBox="0 0 16 16" aria-hidden="true"><path d="M1 3h14v10H1zm1.5 1.5L8 9l5.5-4.5z"/></svg>
        maren@lanternfielddrinks.com
      </p>
      <p class="contact__address">48 Millrace Lane,<br>Fairbrook, US 20418</p>
    </div>
    <div class="back__strip"></div>
    <div class="back__tab">www.lanternfielddrinks.com</div>
  </section>
</body>
</html>
```